Food broker, trader, wholesaler, liquidator looking for a 5 pages website

Looking for a 5 pages website design. We are food brokers, traders, wholesaler and closeout buyer working with manufacturers, distributors, importers sell to retailers, food service operators and industrial (ingredients). We help market their products. We are a resource for those who need a solution in the distribution/selling/placement of food on the shelves, kitchens and pantries. Whether we open new accounts with new products or sell short dated inventory, we know where to go and get results.

Target Market(s)

Food manufacturers, food distributors, food brokers

Coding

Coded - Design and coding required

Number of Pages Required

4 page

Font styles to use
Serif

Requirements
Must have
• Food-food production-warehouse-Food packaging-people meeting-trucks-supermarket shelves-

```html
<!DOCTYPE html>
<html lang="en">
<head>
<meta charset="utf-8">
<title>Meridian Trade Foods</title>
<link href="https://fonts.googleapis.com/css2?family=Merriweather:wght@300;400;700;900&family=Roboto:wght@400;500;700&display=swap" rel="stylesheet">
<style>
:root{
  --navy:#15155c;
  --navy-deep:#0f0f48;
  --navy-ring:#2a2a78;
  --lavender:#e9e9f1;
  --rule:#a6a6c6;
  --text:#6a6a6a;
  --ink:#222;
  --white:#fff;
}
*{margin:0;padding:0;box-sizing:border-box}
html,body{width:1200px;height:3933px;overflow:hidden;background:var(--white)}
body{font-family:'Roboto',Arial,sans-serif;color:var(--text)}
.page{position:relative;width:1200px;height:3933px;overflow:hidden}
.abs{position:absolute}

/* header */
.topbar{position:absolute;left:0;top:0;width:1200px;height:43px}
.topbar-text{position:absolute;left:611px;top:13px;font-size:13px;color:var(--white);letter-spacing:.2px;white-space:nowrap}
.topbar-text svg{vertical-align:-2px;margin-right:5px}
.brand{position:absolute;left:142px;top:34px;display:flex;align-items:center;gap:12px}
.brand-dot{width:52px;height:52px;border-radius:50%;background:var(--navy)}
.brand-name{font-family:'Merriweather',Georgia,serif;font-weight:700;font-size:15px;color:var(--navy);letter-spacing:.4px}
.nav{position:absolute;top:78px;left:0;width:1200px;height:20px}
.nav a{position:absolute;font-size:15px;font-weight:500;color:#2a2a2a;text-decoration:none;white-space:nowrap}
.nav-active-bar{position:absolute;left:508px;top:120px;width:48px;height:5px;background:var(--navy)}

/* hero */
.hero-photo{position:absolute;left:0;top:125px;width:1200px;height:680px;
  background:
   linear-gradient(125deg,rgba(255,120,60,.0) 55%,rgba(230,100,60,.55) 70%,rgba(60,120,210,.6) 82%,rgba(220,80,60,.45) 92%,rgba(20,40,60,.3) 100%),
   linear-gradient(180deg,#123238 0%,#0e2a30 50%,#0b2228 100%)}
.hero-title{position:absolute;left:145px;top:252px;font-family:'Merriweather',Georgia,serif;font-weight:700;font-size:60px;line-height:62px;color:var(--white);letter-spacing:1px}
.hero-sub{position:absolute;left:145px;top:402px;font-size:21px;line-height:30px;color:var(--white)}
.btn{position:absolute;display:flex;align-items:center;justify-content:center;gap:9px;background:var(--navy);color:var(--white);font-weight:700;font-size:17px;border-radius:30px;letter-spacing:.3px}
.hero-dots{position:absolute;left:145px;top:618px;display:flex;gap:6px}
.hero-dots span{width:10px;height:10px;border-radius:50%;background:var(--white)}
.hero-dots span.off{background:transparent;border:1.5px solid var(--white)}

/* sections */
.kicker{position:absolute;left:0;width:1200px;text-align:center;font-family:'Merriweather',Georgia,serif;font-weight:300;font-size:40px;color:#1b1b2e;letter-spacing:.5px}
.heading{position:absolute;left:0;width:1200px;text-align:center;font-family:'Merriweather',Georgia,serif;font-weight:700;font-size:40px;color:var(--navy);letter-spacing:.5px}
.rule{position:absolute;left:578px;width:44px;height:3px;background:var(--rule)}
.lead{position:absolute;left:195px;width:810px;text-align:center;font-size:14.5px;line-height:31px;color:var(--text)}
.faint-ship{position:absolute;opacity:.13;border-radius:4px}

/* service circles */
.service{position:absolute;border-radius:50%;text-align:center;display:flex;flex-direction:column;align-items:center}
.service.light{background:var(--white);border:9px solid #f1f1f4;box-shadow:0 0 0 2px #dcdce4,0 6px 18px rgba(0,0,0,.08)}
.service.dark{background:var(--navy-deep);border:14px solid var(--navy-ring);color:var(--white)}
.service h3{font-size:18.5px;font-weight:700;color:#1b1b1b;line-height:24px;letter-spacing:.2px}
.service.dark h3{color:var(--white)}
.service p{font-size:12.5px;line-height:22px;color:#555;margin-top:10px}
.service.dark p{color:#dcdcf0}
.service .more{font-size:14.5px;font-weight:700;color:var(--navy);margin-top:14px}
.service.dark .more{color:var(--white)}

/* contact form */
.field{position:absolute;border:1.5px solid #8f8fa8;border-radius:22px;font-size:12px;color:#555;padding:11px 0 0 27px;background:var(--white)}

/* footer */
.footer-info{position:absolute;top:3680px;display:flex;align-items:center;gap:16px;color:var(--white);font-size:13.5px;line-height:21px}
.footer-icon{width:42px;height:42px;border-radius:50%;border:1.5px solid rgba(255,255,255,.7);display:flex;align-items:center;justify-content:center}
.footer-nav{position:absolute;top:3766px;left:0;width:1200px;text-align:center;color:var(--white);font-size:15px;font-weight:700;word-spacing:2px}
.footer-nav span{margin:0 12px}
.footer-line{position:absolute;left:0;top:3848px;width:1200px;height:1px;background:rgba(255,255,255,.15)}
.copyright{position:absolute;left:145px;top:3886px;color:var(--white);font-size:13px}
.social{position:absolute;top:3880px;width:29px;height:29px;border-radius:50%;border:1.5px solid rgba(255,255,255,.8)}
</style>
</head>
<body>
<div class="page">

  <!-- header -->
  <svg class="topbar" width="1200" height="43" viewBox="0 0 1200 43">
    <polygon points="524,0 1200,0 1200,43 572,43" fill="var(--navy)"/>
  </svg>
  <div class="topbar-text">
    <svg width="12" height="12" viewBox="0 0 24 24"><path fill="#fff" d="M6.6 10.8a15 15 0 006.6 6.6l2.2-2.2c.3-.3.7-.4 1-.2 1.1.4 2.3.6 3.6.6.6 0 1 .4 1 1V20c0 .6-.4 1-1 1A17 17 0 013 4c0-.6.4-1 1-1h3.5c.6 0 1 .4 1 1 0 1.3.2 2.5.6 3.6.1.3 0 .7-.2 1z"/></svg>CALL US : 1 800 555 0142 &nbsp;|&nbsp; <svg width="13" height="11" viewBox="0 0 26 20"><rect x="1.5" y="1.5" width="23" height="17" rx="2" fill="none" stroke="#fff" stroke-width="2.5"/><path d="M2 3l11 8 11-8" fill="none" stroke="#fff" stroke-width="2.5"/></svg>EMAIL : info@meridiantradefoods.com
  </div>
  <div class="brand"><span class="brand-dot"></span><span class="brand-name">MERIDIAN TRADE FOODS</span></div>
  <nav class="nav">
    <a style="left:508px">HOME</a>
    <a style="left:594px">ABOUT US</a>
    <a style="left:710px">WHAT WE DO</a>
    <a style="left:848px">CONTACT</a>
    <a style="left:959px">GIVING BACK</a>
  </nav>
  <div class="nav-active-bar"></div>

  <!-- hero -->
  <div class="hero-photo" role="img" aria-label="Aerial view of a container ship loaded with colourful containers on dark sea"></div>
  <h1 class="hero-title">MERIDIAN<br>TRADE FOODS</h1>
  <p class="hero-sub">Lorem ipsum dolor sit amet conse<br>ctetur adipiscing elit seddo</p>
  <div class="btn" style="left:145px;top:504px;width:195px;height:59px">GET STARTED
    <svg width="16" height="16" viewBox="0 0 20 20"><circle cx="10" cy="10" r="9" fill="#fff"/><path d="M8 5.5l4.5 4.5L8 14.5" fill="none" stroke="var(--navy)" stroke-width="2.6"/></svg></div>
  <div class="hero-dots"><span></span><span></span><span class="off"></span><span></span><span></span></div>

  <!-- backgrounds and curves -->
  <svg class="abs" style="left:0;top:0" width="1200" height="3933" viewBox="0 0 1200 3933">
    <path d="M0,1390 Q600,1230 1200,1390 L1200,2890 Q600,2810 0,2890 Z" fill="var(--lavender)"/>
    <path d="M0,808 Q600,700 1200,808 L1200,830 L0,830 Z" fill="#fff"/>
    <path d="M0,796 Q600,712 1200,796" fill="none" stroke="var(--navy)" stroke-width="6"/>
    <path d="M0,808 Q600,724 1200,808" fill="none" stroke="var(--navy)" stroke-width="2"/>
    <circle cx="600" cy="744" r="40" fill="#fff"/>
    <circle cx="600" cy="744" r="32" fill="var(--navy)"/>

    <path d="M0,3540 Q600,3470 1200,3540 L1200,3933 L0,3933 Z" fill="var(--navy)"/>
    <path d="M0,3530 Q600,3458 1200,3530" fill="none" stroke="var(--navy)" stroke-width="5"/>
    <path d="M0,3548 Q600,3476 1200,3548" fill="none" stroke="#fff" stroke-width="2"/>
    <circle cx="600" cy="3639" r="40" fill="#fff"/>
    <circle cx="600" cy="3639" r="32" fill="var(--navy)"/>
  </svg>

  <!-- welcome -->
  <div class="faint-ship" style="left:122px;top:1140px;width:940px;height:200px;background:linear-gradient(90deg,#b44 0%,#47c 25%,#c84 50%,#4a7 75%,#888 100%)" role="img" aria-label="Faint container ship in the background"></div>
  <div class="kicker" style="top:857px">WELCOME TO</div>
  <div class="heading" style="top:910px">MERIDIAN TRADE FOODS</div>
  <div class="rule" style="top:986px"></div>
  <p class="lead" style="top:1030px">Meridian Trade Foods works with food manufacturers, brand owners, distributors and wholesalers market their products. Retail, Food Service and Industrial ingredients. Founded in 2008, Meridian Trade Foods started with the distribution of gluten free products understanding the need to provide access to unique flavors and products for the celiac consumers. From this, we expanded into deli, dairy, groceries, frozen and beverages.</p>

  <!-- services -->
  <div class="service light" style="left:155px;top:1237px;width:300px;height:300px;padding-top:31px">
    <svg width="86" height="76" viewBox="0 0 86 76" fill="none" stroke="#222" stroke-width="2.2"><rect x="6" y="34" width="30" height="20" rx="2"/><path d="M36 40l22-10v28L36 48"/><path d="M12 54l4 14h8l-3-14"/><circle cx="66" cy="18" r="10"/><path d="M62 22l8-8M63 15h.1M69 21h.1"/><path d="M50 62h30M54 70h22"/></svg>
    <h3 style="margin-top:18px">SALES &amp; MARKETING</h3>
    <p>we connect food buyers and sellers<br>through a dedicated approach.</p>
    <div class="more">READ MORE</div>
  </div>
  <div class="service light" style="left:745px;top:1237px;width:300px;height:300px;padding-top:34px">
    <svg width="88" height="70" viewBox="0 0 88 70" fill="none" stroke="#222" stroke-width="2.2"><rect x="10" y="4" width="68" height="44" rx="3"/><rect x="15" y="9" width="58" height="34"/><path d="M2 56h84l-5 8H7z"/><path d="M22 38V30M32 38V24M42 38V28M52 38V20M62 38V16"/><path d="M20 28l12-8 10 5 20-14"/></svg>
    <h3 style="margin-top:18px">TRADING</h3>
    <p>we purchase goods anywhere and<br>ship them Nationwide and Export</p>
    <div class="more">READ MORE</div>
  </div>
  <div class="service dark" style="left:435px;top:1222px;width:330px;height:330px;padding-top:26px">
    <svg width="80" height="78" viewBox="0 0 80 78" fill="none" stroke="#fff" stroke-width="2.2"><rect x="8" y="4" width="26" height="22"/><rect x="40" y="4" width="26" height="22"/><path d="M21 4v8M53 4v8"/><circle cx="22" cy="40" r="7"/><path d="M10 60c0-8 6-12 12-12s12 4 12 12"/><rect x="38" y="48" width="32" height="24"/><path d="M54 48v10M4 74h72"/></svg>
    <h3 style="margin-top:12px">CLOSEOUT/<br>EXCESS INVENTORY</h3>
    <p>we buy closeouts and excess inventory for<br>prisons, outlet stores and discounters.</p>
    <div class="more">READ MORE</div>
  </div>

  <!-- featured cycle -->
  <div class="kicker" style="top:1651px">OUR</div>
  <div class="heading" style="top:1704px">FEATURED CYCLE</div>
  <div class="rule" style="top:1779px"></div>
  <p class="lead" style="top:1824px">Lorem ipsum dolor sit amet, consectetur adipiscing elit, sed do eiusmod tempor incididunt ut labore et dolore magna aliqua. Ut enim ad minim veniam, quis nostrud exercitation ullamco laboris nisi ut aliquip ex ea commodo consequat. Duis aute irure dolor in reprehenderit in voluptate velit esse cillum dolore eu fugiat nulla pariatur. Excepteur sint occaecat cupidatat non proident, sunt in culpa qui officia deserunt mollit anim id est laborum</p>

  <svg class="abs" style="left:0;top:1950px" width="1200" height="850" viewBox="0 0 1200 850" font-family="Roboto, Arial, sans-serif" font-weight="700" font-size="22" fill="#222" text-anchor="middle">
    <defs>
      <filter id="cardShadow" x="-20%" y="-20%" width="140%" height="140%"><feDropShadow dx="0" dy="3" stdDeviation="5" flood-color="#000" flood-opacity=".15"/></filter>
      <linearGradient id="gWarehouse" x1="0" y1="0" x2="1" y2="1"><stop offset="0" stop-color="#6b4a30"/><stop offset=".5" stop-color="#c9a24a"/><stop offset="1" stop-color="#8a6a48"/></linearGradient>
      <linearGradient id="gProduction" x1="0" y1="0" x2="1" y2="1"><stop offset="0" stop-color="#e99a2e"/><stop offset=".5" stop-color="#c9ccd2"/><stop offset="1" stop-color="#5e8fc8"/></linearGradient>
      <linearGradient id="gPackaging" x1="0" y1="0" x2="1" y2="1"><stop offset="0" stop-color="#9aa4b2"/><stop offset=".5" stop-color="#2f5fa8"/><stop offset="1" stop-color="#6a7480"/></linearGradient>
      <linearGradient id="gFood" x1="0" y1="0" x2="1" y2="1"><stop offset="0" stop-color="#3d8a2c"/><stop offset=".45" stop-color="#e0672a"/><stop offset="1" stop-color="#b8241f"/></linearGradient>
      <linearGradient id="gPeople" x1="0" y1="0" x2="1" y2="1"><stop offset="0" stop-color="#d9d9dd"/><stop offset=".5" stop-color="#7d8796"/><stop offset="1" stop-color="#eeeeef"/></linearGradient>
      <linearGradient id="gShelves" x1="0" y1="0" x2="1" y2="1"><stop offset="0" stop-color="#c0392b"/><stop offset=".5" stop-color="#d8c9a0"/><stop offset="1" stop-color="#3f8e4a"/></linearGradient>
      <linearGradient id="gTrucks" x1="0" y1="0" x2="0" y2="1"><stop offset="0" stop-color="#8fb1d6"/><stop offset=".6" stop-color="#4d5d78"/><stop offset="1" stop-color="#9a9ea6"/></linearGradient>
    </defs>

    <!-- Warehouse 600,208 -->
    <polygon points="600,63 745,208 600,353 455,208" fill="#fff" filter="url(#cardShadow)"/>
    <g role="img" aria-label="Warehouse worker scanning stacked boxes"><polygon points="600,63 745,208 701,252 499,252 455,208" fill="url(#gWarehouse)"/></g>
    <text x="603" y="287">Warehouse</text>

    <!-- Food Production 447,361 -->
    <polygon points="447,216 592,361 447,506 302,361" fill="#fff" filter="url(#cardShadow)"/>
    <g role="img" aria-label="Food production line with gloved hands"><polygon points="447,216 592,361 548,405 346,405 302,361" fill="url(#gProduction)"/></g>
    <text x="450" y="420">Food</text><text x="450" y="442">Production</text>

    <!-- Food Packaging 753,361 -->
    <polygon points="753,216 898,361 753,506 608,361" fill="#fff" filter="url(#cardShadow)"/>
    <g role="img" aria-label="Food packaging conveyor with trays"><polygon points="753,216 898,361 854,405 652,405 608,361" fill="url(#gPackaging)"/></g>
    <text x="756" y="410">Food</text><text x="756" y="432">Packaging</text>

    <!-- Food 294,514 -->
    <polygon points="294,369 439,514 294,659 149,514" fill="#fff" filter="url(#cardShadow)"/>
    <g role="img" aria-label="Fresh fruits, vegetables and grains"><polygon points="294,369 439,514 395,558 193,558 149,514" fill="url(#gFood)"/></g>
    <text x="298" y="598">Food</text>

    <!-- People Meeting 906,514 -->
    <polygon points="906,369 1051,514 906,659 761,514" fill="#fff" filter="url(#cardShadow)"/>
    <g role="img" aria-label="Business people shaking hands at a meeting"><polygon points="906,369 1051,514 1007,558 805,558 761,514" fill="url(#gPeople)"/></g>
    <text x="911" y="578">People</text><text x="911" y="600">Meeting</text>

    <!-- Supermarket Shelves 447,667 -->
    <polygon points="447,522 592,667 447,812 302,667" fill="#fff" filter="url(#cardShadow)"/>
    <g role="img" aria-label="Supermarket aisle with stocked shelves"><polygon points="447,522 592,667 548,711 346,711 302,667" fill="url(#gShelves)"/></g>
    <text x="446" y="730">Supermarket</text><text x="446" y="752">Shelves</text>

    <!-- Trucks 753,667 -->
    <polygon points="753,522 898,667 753,812 608,667" fill="#fff" filter="url(#cardShadow)"/>
    <g role="img" aria-label="Freight truck driving on a highway"><polygon points="753,522 898,667 854,711 652,711 608,667" fill="url(#gTrucks)"/></g>
    <text x="752" y="748">Trucks</text>

    <!-- centre emblem -->
    <ellipse cx="600" cy="510" rx="92" ry="68" fill="var(--navy)"/>
    <text x="600" y="505" fill="#fff" font-family="Merriweather, Georgia, serif" font-size="15">MERIDIAN</text>
    <text x="600" y="526" fill="#fff" font-family="Merriweather, Georgia, serif" font-size="15">TRADE FOODS</text>
  </svg>

  <!-- contact -->
  <div class="kicker" style="top:2968px">CONTACT</div>
  <div class="heading" style="top:3022px">MERIDIAN TRADE FOODS</div>
  <div class="rule" style="top:3099px"></div>
  <div class="faint-ship" style="left:150px;top:3355px;width:900px;height:170px;background:linear-gradient(90deg,#b44 0%,#47c 25%,#c84 50%,#4a7 75%,#888 100%)" role="img" aria-label="Faint container ship in the background"></div>
  <div class="field" style="left:218px;top:3155px;width:372px;height:42px">Enter Name</div>
  <div class="field" style="left:609px;top:3155px;width:372px;height:42px">Enter Email</div>
  <div class="field" style="left:218px;top:3215px;width:372px;height:42px">Phone</div>
  <div class="field" style="left:609px;top:3215px;width:372px;height:42px">Address</div>
  <div class="field" style="left:218px;top:3275px;width:763px;height:75px">Message</div>
  <div class="btn" style="left:475px;top:3393px;width:250px;height:57px">SUBMIT MESSAGE
    <svg width="16" height="16" viewBox="0 0 20 20"><circle cx="10" cy="10" r="9" fill="#fff"/><path d="M8 5.5l4.5 4.5L8 14.5" fill="none" stroke="var(--navy)" stroke-width="2.6"/></svg></div>

  <!-- footer -->
  <div class="footer-info" style="left:236px">
    <span class="footer-icon"><svg width="14" height="18" viewBox="0 0 14 20"><path d="M7 1a6 6 0 016 6c0 4.5-6 12-6 12S1 11.5 1 7a6 6 0 016-6z" fill="none" stroke="#fff" stroke-width="1.8"/><circle cx="7" cy="7" r="2" fill="#fff"/></svg></span>
    <span>314,At vero eos et accu<br>samus et iusto odio dimos ducimu</span>
  </div>
  <div class="footer-info" style="left:542px">
    <span class="footer-icon"><svg width="16" height="16" viewBox="0 0 24 24"><path fill="#fff" d="M6.6 10.8a15 15 0 006.6 6.6l2.2-2.2c.3-.3.7-.4 1-.2 1.1.4 2.3.6 3.6.6.6 0 1 .4 1 1V20c0 .6-.4 1-1 1A17 17 0 013 4c0-.6.4-1 1-1h3.5c.6 0 1 .4 1 1 0 1.3.2 2.5.6 3.6.1.3 0 .7-.2 1z"/></svg></span>
    <span>1 800 555 0142</span>
  </div>
  <div class="footer-info" style="left:727px">
    <span class="footer-icon"><svg width="17" height="13" viewBox="0 0 26 20"><rect x="1" y="1" width="24" height="18" rx="2" fill="#fff"/><path d="M2 3l11 8 11-8" fill="none" stroke="var(--navy)" stroke-width="2.2"/></svg></span>
    <span>info@meridiantradefoods.com</span>
  </div>
  <div class="footer-nav">HOME<span>/</span>ABOUT US<span>/</span>WHAT WE DO<span>/</span>CONTACT<span>/</span>GIVING BACK</div>
  <div class="footer-line"></div>
  <div class="copyright">Copyrights © 2020, Meridian Trade Foods.All rights reserved.</div>
  <span class="social" style="left:916px"></span>
  <span class="social" style="left:951px"></span>
  <span class="social" style="left:986px"></span>
  <span class="social" style="left:1021px"></span>

</div>
</body>
</html>
```